automotive repair and collision repair shop card

our company is called K.L Motor service we are a automotive repair company
we also do government inspections. the company information is on the cards. I would like you to use my new logo and create a new card and use the information from my old card. Good Luck!!

Industry/Entity Type

Car Repair

Contact Information for Business Card

Address: #417-18842 52 Ave, Surrey, BC V5K 8R3
Phone:(604) 555-0187
fax 604 555 0193
website www.klmotorworks.example

Font styles to use
Serif
Sans Serif

Requirements
Must have
• all the information
Should not have
• the owner and there name

```html
<!DOCTYPE html>
<html lang="en">
<head>
<meta charset="utf-8">
<title>K.L Motor service – Business Card</title>
<link rel="stylesheet" href="https://fonts.googleapis.com/css2?family=Oswald:wght@300;400;500&display=swap">
<style>
  :root {
    --stage: #e6e4e1;
    --ink: #111111;
    --ink-soft: #555555;
    --paper: #f7f7f6;
    --paper-shade: #e9e9e8;
    --night: #050505;
    --night-lift: #2a2a2a;
    --chrome: #cfcfcf;
    --white: #ffffff;
  }
  * { margin: 0; padding: 0; box-sizing: border-box; }
  html, body {
    width: 1200px; height: 902px; overflow: hidden;
    background: var(--stage);
    font-family: "Oswald", "Arial Narrow", sans-serif;
  }
  .stage {
    width: 1200px; height: 902px;
    display: flex; align-items: center; justify-content: center; gap: 40px;
  }
  .card {
    width: 540px; height: 309px; position: relative; overflow: hidden;
    box-shadow: 0 10px 28px rgba(0,0,0,.22);
  }

  /* Front */
  .card-front {
    background: linear-gradient(160deg, var(--night-lift) 0%, var(--night) 40%, var(--night) 100%);
  }
  .front-title {
    position: absolute; top: 26px; right: 30px; text-align: right; color: var(--white);
  }
  .front-title .brand {
    font-size: 42px; font-weight: 400; letter-spacing: 1px; text-transform: uppercase; line-height: 1;
  }
  .front-title .tagline {
    font-size: 15px; font-weight: 300; letter-spacing: .5px; margin-top: 4px;
  }
  .front-photo {
    position: absolute; left: 0; right: 0; bottom: 0; height: 190px;
    background:
      radial-gradient(ellipse 60% 40% at 55% 55%, #3a3a3a 0%, #1c1c1c 60%, transparent 75%),
      linear-gradient(180deg, var(--night) 0%, #1a1a1a 45%, #9a9a9a 78%, var(--chrome) 100%);
  }

  /* Back */
  .card-back { background: linear-gradient(135deg, var(--white) 0%, var(--paper) 55%, var(--paper-shade) 100%); }
  .divider { position: absolute; inset: 0; }
  .back-logo {
    position: absolute; left: 36px; top: 168px; color: var(--ink);
  }
  .back-logo .brand {
    font-size: 31px; font-weight: 400; text-transform: uppercase; letter-spacing: .5px; line-height: 1;
  }
  .back-logo .tagline {
    font-size: 12px; font-weight: 300; color: var(--ink-soft); text-align: right; margin-top: 4px;
  }
  .contact-list {
    position: absolute; left: 330px; top: 138px; list-style: none;
  }
  .contact-list li {
    display: flex; align-items: flex-start; gap: 9px;
    font-size: 12.5px; font-weight: 400; color: var(--ink); line-height: 1.25; margin-bottom: 5px;
  }
  .contact-list .icon {
    flex: 0 0 14px; width: 14px; height: 14px; background: var(--ink);
    display: flex; align-items: center; justify-content: center; margin-top: 1px;
  }
</style>
</head>
<body>
<main class="stage">

  <section class="card card-front">
    <div class="front-photo" role="img" aria-label="Photograph of a dark grey sports car in side view on a light studio floor"></div>
    <div class="front-title">
      <div class="brand">K.L Motor service</div>
      <div class="tagline">One Stop Repair Shop</div>
    </div>
  </section>

  <section class="card card-back">
    <svg class="divider" width="540" height="309" viewBox="0 0 540 309" aria-hidden="true">
      <line x1="290" y1="0" x2="300" y2="309" stroke="#bdbdbd" stroke-width="1"/>
    </svg>

    <div class="back-logo">
      <div class="brand">K.L Motor service</div>
      <div class="tagline">One Stop Repair Shop</div>
    </div>

    <ul class="contact-list">
      <li><span class="icon"><svg width="10" height="10" viewBox="0 0 10 10"><path d="M2 1h2l1 2-1.2 1a5 5 0 0 0 2.2 2.2L7 5l2 1v2a1 1 0 0 1-1 1A7 7 0 0 1 1 2a1 1 0 0 1 1-1z" fill="#fff"/></svg></span>(604) 555-0187</li>
      <li><span class="icon"><svg width="10" height="10" viewBox="0 0 10 10"><rect x="2.5" y="1" width="5" height="3" fill="#fff"/><rect x="1" y="4" width="8" height="3.5" fill="#fff"/><rect x="3" y="6.5" width="4" height="2.5" fill="#fff"/></svg></span>604 555 0193</li>
      <li><span class="icon"><svg width="10" height="10" viewBox="0 0 10 10"><circle cx="5" cy="5" r="3.8" fill="none" stroke="#fff" stroke-width="1"/><ellipse cx="5" cy="5" rx="1.6" ry="3.8" fill="none" stroke="#fff" stroke-width=".8"/><line x1="1.2" y1="5" x2="8.8" y2="5" stroke="#fff" stroke-width=".8"/></svg></span>www.klmotorworks.example</li>
      <li><span class="icon"><svg width="10" height="10" viewBox="0 0 10 10"><rect x="1" y="2.5" width="8" height="5.5" fill="#fff"/><path d="M1 2.5l4 3 4-3" fill="none" stroke="#111" stroke-width=".9"/></svg></span>info@klmotorworks.example</li>
      <li><span class="icon"><svg width="10" height="10" viewBox="0 0 10 10"><path d="M5 9.5S1.8 6 1.8 4a3.2 3.2 0 0 1 6.4 0c0 2-3.2 5.5-3.2 5.5z" fill="#fff"/><circle cx="5" cy="4" r="1.1" fill="#111"/></svg></span>#417-18842 52 Ave, Surrey,<br>BC V5K 8R3</li>
    </ul>
  </section>

</main>
</body>
</html>
```